indépendant en tant que Massothérapeute et Préparateur Mental, j'ai besoin de ...

Massothérapeute et préparateur mental indépendant, je recherche une carte de visite sobre et dynamique, sans images liées au massage ou à la préparation mentale mais intégrant mon logo. Les couleurs que j'aime bien sont : Blanc, gris, anthracite, noir et jaune

Contact Information for Business Card

carte de préférence Horizontale
neutre qui puisse toucher le deux domaines Massothérapie et préparation mentale

Requirements
Must have
• mon projet doit intégrer au recto:
LOGO
Loïc Bardèze
078 513 26 48
info@loicbardeze.ch
et éventuellement www.loicbardeze.ch

et au verso les deux adresses:

Chemin des Ormilles 7B
1462 Vaulmont-les-Prés

Route de la Gravière 9
1700 Fribourg

Should not have
• mon projet ne doit pas contenir d'image en liens avec le massage ni la préparation mentale.

```html
<!DOCTYPE html>
<html lang="fr">
<head>
<meta charset="utf-8">
<title>Loïc Bardèze – cartes de visite</title>
<link rel="stylesheet" href="https://fonts.googleapis.com/css2?family=Montserrat:wght@500;600;700&family=Arimo&display=swap">
<style>
  :root {
    --backdrop: #acacac;
    --paper: #ffffff;
    --anthracite: #221f20;
    --ink: #1b1b1b;
    --ink-reverse: #ffffff;
  }
  * { margin: 0; padding: 0; box-sizing: border-box; }
  html, body { width: 1065px; height: 1200px; overflow: hidden; }
  body { background: var(--backdrop); position: relative; font-family: "Arimo", Arial, sans-serif; }

  .card { position: absolute; width: 583px; height: 363px; }
  .card--front {
    left: 292px; top: 218px;
    background: var(--paper); color: var(--ink);
    border-radius: 0 180px 180px 0 / 0 50% 50% 0;
  }
  .card--back {
    left: 263px; top: 623px;
    background: var(--anthracite); color: var(--ink-reverse);
    border-radius: 180px 0 0 180px / 50% 0 0 50%;
  }

  .holder-name {
    position: absolute; left: 254px; top: 44px;
    font-family: "Montserrat", sans-serif; font-weight: 700;
    font-size: 21px; letter-spacing: 0.2px;
  }
  .contact-list { position: absolute; left: 255px; top: 84px; list-style: none; }
  .contact-list li {
    display: flex; align-items: center; gap: 7px;
    height: 21px; font-size: 16.5px;
  }
  .contact-list svg { width: 15px; height: 15px; flex: none; fill: var(--ink); }

  .brand { position: absolute; display: flex; align-items: center; gap: 16px; }
  .brand__dot { width: 46px; height: 46px; border-radius: 50%; background: currentColor; flex: none; }
  .brand__name {
    font-family: "Montserrat", sans-serif; font-weight: 600;
    font-size: 23px; line-height: 1;
  }
  .brand__role {
    font-family: "Montserrat", sans-serif; font-weight: 500;
    font-size: 9px; letter-spacing: 0.35px; text-transform: uppercase;
    margin-top: 5px;
  }
  .card--front .brand { left: 192px; top: 166px; }
  .card--back .brand { left: 211px; top: 156px; }

  .address {
    position: absolute; left: 255px;
    font-size: 16.5px; line-height: 21px; font-style: normal;
  }
  .address--first { top: 234px; }
  .address--second { top: 282px; left: 256px; }
</style>
</head>
<body>
  <section class="card card--front" aria-label="Recto">
    <h1 class="holder-name">LOÏC BARDÈZE</h1>
    <ul class="contact-list">
      <li>
        <svg viewBox="0 0 24 24" aria-hidden="true"><path d="M6.6 10.8a15.1 15.1 0 0 0 6.6 6.6l2.2-2.2c.3-.3.7-.4 1-.2 1.1.4 2.3.6 3.6.6.6 0 1 .4 1 1V20c0 .6-.4 1-1 1A17 17 0 0 1 3 4c0-.6.4-1 1-1h3.5c.6 0 1 .4 1 1 0 1.3.2 2.5.6 3.6.1.3 0 .7-.2 1z"/></svg>
        078 513 26 48
      </li>
      <li>
        <svg viewBox="0 0 24 24" aria-hidden="true"><path d="M2 5h20v14H2zm2 2v.3l8 5.2 8-5.2V7zm0 2.7V17h16V9.7l-8 5.2z"/></svg>
        info@loicbardeze.ch
      </li>
      <li>
        <svg viewBox="0 0 24 24" aria-hidden="true"><path d="M12 2a10 10 0 1 0 0 20 10 10 0 0 0 0-20zm6.9 6h-3a15 15 0 0 0-1.3-3.9A8 8 0 0 1 18.9 8zM12 4c.8 1.2 1.5 2.5 1.9 4h-3.8c.4-1.5 1.1-2.8 1.9-4zM4.3 14a8 8 0 0 1 0-4h3.4a16 16 0 0 0 0 4zm.8 2h3a15 15 0 0 0 1.3 3.9A8 8 0 0 1 5.1 16zm3-8h-3a8 8 0 0 1 4.3-3.9A15 15 0 0 0 8.1 8zM12 20c-.8-1.2-1.5-2.5-1.9-4h3.8c-.4 1.5-1.1 2.8-1.9 4zm2.3-6H9.7a14 14 0 0 1 0-4h4.6a14 14 0 0 1 0 4zm.3 5.9a15 15 0 0 0 1.3-3.9h3a8 8 0 0 1-4.3 3.9zm1.7-5.9a16 16 0 0 0 0-4h3.4a8 8 0 0 1 0 4z"/></svg>
        www.loicbardeze.ch
      </li>
    </ul>

    <div class="brand">
      <span class="brand__dot" aria-hidden="true"></span>
      <div>
        <div class="brand__name">Loïc Bardèze</div>
        <div class="brand__role">Massothérapeute / Préparateur Mental</div>
      </div>
    </div>

    <address class="address address--first">Chemin des Ormilles 7B<br>1462 Vaulmont-les-Prés</address>
    <address class="address address--second">Route de la Gravière 9<br>1725 Grandfey</address>
  </section>

  <section class="card card--back" aria-label="Verso">
    <div class="brand">
      <span class="brand__dot" aria-hidden="true"></span>
      <div>
        <div class="brand__name">Loïc Bardèze</div>
        <div class="brand__role">Massothérapeute / Préparateur Mental</div>
      </div>
    </div>
  </section>
</body>
</html>
```